Business Card & Email Signature Design || Upmarket + Luxury

Rima Vale Honey, a New Zealand Manuka Honey company needs a Business Card & Email Signature design.

Our logo's are attached in Gold & Black versions, feel free to be creative with how you use the logo and it's patterns in your design.

Style:
- Looking for an Elegant, Luxurious, Upmarket feel.
- Black/Matte Black Card, Gold Foil, UV Embossing

Information to Add:

- Logo
- Company Name: Rima Vale Honey
- Name: Martin Holloway
- Title: Creative Director
- Phone: +64 2815 96 417
- Email: martin@rimavalehoney.example.nz
- Website: www.rimavalehoney.example.nz

- Socials: ***For email Signature Only***
- Facebook: https://www.facebook.com/rimavalehoney/
- Instagram: https://www.instagram.com/rimavalehoney/

Target Market(s)

Asia/Europe Luxury, Upmarket

Contact Information for Business Card

- Logo
- Name: Martin Holloway
- Phone: +64 2815 96 417

Font styles to use
Other font styles liked:
• Champagne & Limousines (Attached)

Requirements
Must have
• Business Card & Email Signature Design.

Looking for a Sleek, Luxury, Upmarket Design.

```html
<!DOCTYPE html>
<html lang="en">
<head>
<meta charset="utf-8">
<title>Rima Vale Honey – Business Card</title>
<link rel="stylesheet" href="https://fonts.googleapis.com/css2?family=Cinzel:wght@400&family=Josefin+Sans:wght@300&family=Open+Sans:wght@400&display=swap">
<style>
  :root {
    --backdrop: #b5b3ae;
    --paper: #efefe9;
    --edge: #e0a622;
    --leaf: #7dab1f;
    --ink: #505050;
    --ink-soft: #6a6a6a;
  }
  * { box-sizing: border-box; margin: 0; padding: 0; }
  html, body {
    width: 1200px; height: 960px; overflow: hidden;
    background: var(--backdrop);
  }
  .sheet {
    width: 1200px; height: 960px;
    display: flex; flex-direction: column;
    align-items: center; justify-content: center; gap: 44px;
  }
  .card {
    width: 680px; height: 389px;
    background: var(--paper);
    border: 4px solid var(--edge);
    border-radius: 3px;
    box-shadow: 0 10px 28px rgba(0,0,0,0.18);
    display: flex; flex-direction: column;
    align-items: center; justify-content: center;
  }
  /* front */
  .brand-dot {
    width: 74px; height: 74px; border-radius: 50%;
    background: var(--ink);
    margin-bottom: 34px;
  }
  .brand-name {
    font-family: "Josefin Sans", sans-serif;
    font-weight: 300;
    font-size: 38px;
    letter-spacing: 0.22em;
    color: var(--ink);
    text-transform: uppercase;
  }
  /* back */
  .person-name {
    font-family: "Cinzel", serif;
    font-weight: 400;
    font-size: 38px;
    color: var(--leaf);
    letter-spacing: 0.01em;
    line-height: 1;
  }
  .person-title {
    font-family: "Open Sans", sans-serif;
    font-size: 19px;
    color: var(--ink-soft);
    margin-top: 6px;
  }
  .icon-row {
    display: flex; align-items: center; gap: 10px;
    margin: 16px 0 22px;
  }
  .icon-row .rule {
    width: 88px; height: 2px; background: var(--leaf);
  }
  .icon-row .rule.left { margin-right: 6px; }
  .icon-row .rule.right { margin-left: 6px; }
  .icon { width: 34px; height: 34px; display: block; }
  .contact-line {
    font-family: "Open Sans", sans-serif;
    font-size: 19px;
    color: var(--ink);
    line-height: 1.55;
    text-align: center;
  }
</style>
</head>
<body>
<main class="sheet">
  <section class="card card-front">
    <div class="brand-dot"></div>
    <p class="brand-name">Rima Vale Honey</p>
  </section>

  <section class="card card-back">
    <h1 class="person-name">MARTIN HOLLOWAY</h1>
    <p class="person-title">Creative Director</p>
    <div class="icon-row">
      <span class="rule left"></span>
      <svg class="icon" viewBox="0 0 34 34" aria-label="Phone">
        <circle cx="17" cy="17" r="15.5" fill="none" stroke="var(--leaf)" stroke-width="2"/>
        <path d="M12 10.5c1-.8 2-.6 2.5.4l1.2 2.3c.4.8.2 1.5-.5 2l-.9.7c.6 1.7 1.9 3.1 3.6 4l.8-.9c.6-.6 1.3-.7 2-.3l2.3 1.3c.9.5 1 1.6.3 2.4-1.3 1.5-3 1.8-5 .8-3.4-1.8-5.8-4.6-7-8.1-.5-1.8-.1-3.4.7-4.6z" fill="var(--leaf)"/>
      </svg>
      <svg class="icon" viewBox="0 0 34 34" aria-label="Email">
        <circle cx="17" cy="17" r="15.5" fill="none" stroke="var(--leaf)" stroke-width="2"/>
        <rect x="9.5" y="11.5" width="15" height="11" rx="1" fill="var(--leaf)"/>
        <path d="M10 12.5l7 5.5 7-5.5" fill="none" stroke="var(--paper)" stroke-width="1.4"/>
      </svg>
      <svg class="icon" viewBox="0 0 34 34" aria-label="Website">
        <circle cx="17" cy="17" r="15.5" fill="none" stroke="var(--leaf)" stroke-width="2"/>
        <circle cx="17" cy="17" r="7.5" fill="none" stroke="var(--leaf)" stroke-width="1.8"/>
        <ellipse cx="17" cy="17" rx="3.2" ry="7.5" fill="none" stroke="var(--leaf)" stroke-width="1.4"/>
        <path d="M9.5 17h15" stroke="var(--leaf)" stroke-width="1.4"/>
      </svg>
      <span class="rule right"></span>
    </div>
    <p class="contact-line">+64 2815 96 417 | martin@rimavalehoney.example.nz</p>
    <p class="contact-line">www.RimaValeHoney.example.nz</p>
  </section>
</main>
</body>
</html>
```